Web Design for Independent Pet Supply shop.

Larch Critter Depot is a locally owned and operated premium natural pet food store and supply company with 2 thriving retail stores in Bend, Oregon, and a home delivery service. The pet food offered is the best on the market and may be described as “holistic”. Also on offer is a vast selection of toys, training tools, treats, and other supplies, as well as dog washing services that range from "do-it yourself" to "spa." Current site: LarchCritterDepot.com. They need a new, updated and responsive site.
Likes:
Tovanels.com: Natural colors, not loud, pages in motion, simple & clean but very informative.
Dorvikmerin.com: Everything in simple big colorful blocks. The specials run across the top and in motion. This site looks very professional but simple. The information is available several different places.
Plenharvest.com: Again big blocks through out. Very Fun and inviting. Tons of information with videos and recipes and testimonials. Pleasant feel and colors as well.
Dislikes:
Furlix.com: Looks cheap, hate the colors, very busy and over whelming. Hate the old style header bar going across with options. Too many printed words instead of fun images.
Colors should be "natural" tones, warm and soothing. Deep dark blue and greys with earthy wood color.
Do Not Use: Blue violet, violet, red violet

```html
<!DOCTYPE html>
<html lang="en">
<head>
<meta charset="utf-8">
<title>Larch Critter Depot — Diet for a Healthier Pet</title>
<link rel="stylesheet" href="https://fonts.googleapis.com/css2?family=Lobster&family=Open+Sans:ital,wght@0,400;0,600;0,700;1,400&display=swap">
<style>
:root{
  --navy:#0d2550;
  --navy-deep:#081b3d;
  --navy-bar:#061632;
  --gold:#c7a66a;
  --gold-dark:#b88a43;
  --cream:#f3efe6;
  --paper:#f7f4ee;
  --ink:#2d3340;
  --muted:#7c7c7c;
  --white:#ffffff;
}
*{box-sizing:border-box;margin:0;padding:0}
html,body{width:1200px;height:2250px;overflow:hidden;background:var(--paper)}
body{font-family:"Open Sans",Arial,sans-serif;color:var(--ink)}
.canvas{position:relative;width:1200px;height:2250px;overflow:hidden}
.abs{position:absolute}

/* header */
.site-header{position:absolute;left:0;top:0;width:1200px;height:135px;background:var(--cream)}
.tagline{position:absolute;left:98px;top:56px;font-family:"Lobster",cursive;font-size:19px;color:var(--navy)}
.brand{position:absolute;display:flex;align-items:center;gap:10px;font-family:"Open Sans",Arial,sans-serif;font-weight:700;color:var(--gold-dark);white-space:nowrap}
.brand-dot{border-radius:50%;background:var(--gold-dark)}
.header-brand{left:466px;top:50px;font-size:28px}
.header-brand .brand-dot{width:30px;height:30px}
.search{position:absolute;left:842px;top:54px;width:261px;height:33px;background:var(--white);border:1px solid #ddd;border-radius:3px;font-size:11px;color:#999;padding:9px 12px}
.search svg{position:absolute;right:10px;top:10px}

/* nav */
.main-nav{position:absolute;left:0;top:135px;width:1200px;height:60px;background:var(--white);border-top:3px solid var(--gold)}
.main-nav ul{list-style:none;position:relative;height:57px}
.main-nav li{position:absolute;top:0;height:57px;line-height:57px;font-size:13px;color:#333;text-transform:uppercase}
.main-nav li.active{background:var(--navy);color:var(--white);left:99px;width:84px;text-align:center;top:-3px;height:60px;line-height:63px}

/* hero */
.hero{position:absolute;left:0;top:195px;width:1200px;height:492px;background:linear-gradient(90deg,#0d1d45 0%,#1a2d63 45%,#2c3d6b 75%,#24335e 100%)}
.hero-brand{left:98px;top:105px;font-size:30px;color:var(--white)}
.hero-brand .brand-dot{width:30px;height:30px;background:var(--white)}
.hero-title{position:absolute;left:98px;top:155px;font-family:"Lobster",cursive;font-size:41px;color:var(--white);font-weight:400}
.hero-text{position:absolute;left:98px;top:218px;width:460px;font-size:16px;line-height:26px;color:#e6e8ef}
.btn-contact{position:absolute;left:98px;top:317px;width:127px;height:48px;background:var(--gold-dark);color:var(--white);font-size:15px;font-weight:600;line-height:48px;text-align:center;border-radius:3px}
.dots{position:absolute;left:98px;top:397px;display:flex;gap:9px}
.dots span{width:12px;height:12px;border-radius:50%;background:var(--white)}
.dots span:first-child{background:var(--gold-dark)}
.hero-photo{position:absolute;left:590px;top:245px;width:555px;height:535px;border-radius:48% 42% 10% 30%;background:radial-gradient(ellipse at 40% 40%,#e9e6e1 0%,#9a958f 40%,#2a2a2e 75%,rgba(30,30,40,0) 100%)}

/* services */
.services{position:absolute;left:0;top:687px;width:1200px;height:505px;background:var(--paper)}
.section-title{font-size:26px;font-weight:400;text-transform:uppercase}
.services .section-title{position:absolute;left:98px;top:73px;color:var(--ink)}
.services-intro{position:absolute;left:98px;top:112px;width:840px;font-size:13.5px;line-height:23px;color:var(--gold)}
.service-track{position:absolute;left:0;top:180px}
.service{position:absolute;top:0;width:300px}
.service-ring{width:124px;height:124px;border-radius:50%;border:4px solid var(--gold);background:var(--white);display:flex;align-items:center;justify-content:center}
.service-ring .inner{width:104px;height:104px;border-radius:50%;background:#f1efea;display:flex;align-items:center;justify-content:center}
.service-ring.active .inner{background:var(--navy)}
.service h3{margin-top:24px;font-size:14.5px;font-weight:600;color:var(--navy);text-transform:uppercase}
.service p{margin-top:8px;width:295px;font-size:11.5px;line-height:21px;color:var(--muted)}
.btn-more{display:inline-block;margin-top:14px;width:90px;height:33px;line-height:33px;text-align:center;font-size:11px;text-transform:uppercase;color:var(--white);background:var(--gold);border-radius:2px}
.btn-more.dark{background:var(--navy)}

/* products */
.products{position:absolute;left:0;top:1192px;width:1200px;height:505px;background:var(--navy)}
.products .section-title{position:absolute;left:0;width:1200px;top:39px;text-align:center;color:var(--white)}
.product{position:absolute;top:138px;width:222px;height:314px;background:var(--paper);border:3px solid var(--gold)}
.product-photo{height:190px}
.product h4{margin-top:16px;text-align:center;font-size:14.5px;font-weight:400;color:var(--ink);text-transform:uppercase}
.product p{margin:10px auto 0;width:190px;text-align:center;font-size:11.5px;line-height:21px;color:var(--muted)}
.price{position:absolute;left:-6px;top:-26px;width:54px;height:54px;border-radius:50%;background:var(--gold);border:3px solid var(--white);color:var(--white);font-size:12px;font-weight:700;line-height:48px;text-align:center}
.arrow{position:absolute;top:262px}

/* news */
.news{position:absolute;left:0;top:1697px;width:1200px;height:261px;background:var(--white)}
.news-frame{position:absolute;left:99px;top:50px;width:1003px;height:163px;border:5px solid #ddd6c6;background:var(--white)}
.news-photo{position:absolute;left:10px;top:10px;width:513px;height:133px;background:linear-gradient(90deg,#3a3b3e 0%,#8a8378 30%,#c8b9a0 50%,#4a4b4e 52%,#b8a78c 75%,#3d3e41 100%)}
.news-title{position:absolute;left:550px;top:18px;font-size:14.5px;font-weight:700;color:var(--ink);text-transform:uppercase}
.news-text{position:absolute;left:550px;top:47px;width:420px;font-style:italic;font-size:11px;line-height:22px;color:var(--muted)}
.news-more{position:absolute;right:14px;bottom:6px;font-size:10.5px;color:var(--gold);text-transform:uppercase}

/* footer */
.site-footer{position:absolute;left:0;top:1958px;width:1200px;height:240px;background:var(--navy)}
.footer-brand{left:98px;top:30px;font-size:27px}
.footer-brand .brand-dot{width:28px;height:28px}
.footer-about{position:absolute;left:98px;top:80px;width:260px;font-size:11.5px;line-height:21px;color:#e1e4ea}
.footer-head{position:absolute;top:27px;font-size:15.5px;color:#e1e4ea}
.quick-links{position:absolute;left:432px;top:70px;list-style:none}
.quick-links li{font-size:11px;color:#e1e4ea;height:23px;padding-left:18px;position:relative}
.quick-links li::before{content:"›";position:absolute;left:2px;top:-4px;font-size:15px}
.blog-item{position:absolute;left:598px;width:260px;height:62px}
.blog-thumb{position:absolute;left:0;top:0;width:62px;height:58px;border:2px solid var(--white);background:linear-gradient(135deg,#b7865a,#e4c7a1)}
.blog-item h5{position:absolute;left:75px;top:2px;font-size:11px;font-weight:400;color:#e1e4ea}
.blog-item .date{position:absolute;left:75px;top:22px;font-size:11px;color:#c9ceda}
.blog-item .comments{position:absolute;left:75px;top:44px;font-size:11px;color:#c9ceda;display:flex;gap:6px;align-items:center}
.contact-row{position:absolute;left:904px;display:flex;gap:14px;color:#e1e4ea;font-size:11.5px;line-height:20px}
.contact-row.phone{font-size:16px;font-weight:600}

.bottom-bar{position:absolute;left:0;top:2198px;width:1200px;height:52px;background:var(--navy-bar)}
.copyright{position:absolute;left:98px;top:18px;font-size:11px;color:#cfd3dc}
.social{position:absolute;left:933px;top:11px;display:flex;gap:9px}
.social span{width:30px;height:30px;border-radius:50%;border:1.5px solid #cfd3dc}
</style>
</head>
<body>
<div class="canvas">

  <header class="site-header">
    <p class="tagline">Dedicated to a better diet for a healthier pet</p>
    <div class="brand header-brand"><span class="brand-dot"></span>Larch Critter Depot</div>
    <div class="search">Search
      <svg width="12" height="12" viewBox="0 0 12 12"><circle cx="5" cy="5" r="3.6" fill="none" stroke="#c7a66a" stroke-width="1.5"/><line x1="7.7" y1="7.7" x2="11" y2="11" stroke="#c7a66a" stroke-width="1.6"/></svg>
    </div>
  </header>

  <nav class="main-nav">
    <ul>
      <li class="active">Home</li>
      <li style="left:227px">Events</li>
      <li style="left:338px">Blog</li>
      <li style="left:438px">About</li>
      <li style="left:546px">Dog Wash</li>
      <li style="left:679px">Products</li>
      <li style="left:810px">Resources</li>
      <li style="left:946px">Links</li>
      <li style="left:1046px">Contact</li>
    </ul>
  </nav>

  <section class="hero">
    <div class="brand hero-brand abs"><span class="brand-dot"></span>Larch Critter Depot</div>
    <h1 class="hero-title">Diet for a Healthier Pet</h1>
    <p class="hero-text">Sed ut perspiciatis unde omnis iste natus error sit voluptatem eaque ipsa quae ab illo inventore veritatis et quasi architecto beatae vitae dicta sunt explicabo. Nemo enim...</p>
    <div class="btn-contact">Contact Us</div>
    <div class="dots"><span></span><span></span><span></span></div>
  </section>
  <div class="hero-photo" role="img" aria-label="Black and white dog lying behind a red bowl of bone-shaped treats"></div>

  <section class="services">
    <h2 class="section-title">Service We Offer</h2>
    <p class="services-intro">Architecto beatae vitae dicta sunt explicabo. Nemo enim ipsam voluptatem quia voluptas sit aspernatur aut odit aut fugit, sed quia consequuntur magni dolores eos &nbsp;sequi aliquam quaerat v dolorem ipsum nesciunt qui ratione...</p>

    <svg class="abs" style="left:0;top:180px" width="1200" width="1200" height="124" viewBox="0 0 1200 124">
      <line x1="222" y1="62" x2="455" y2="62" stroke="#c7a66a" stroke-width="3"/>
      <line x1="578" y1="62" x2="812" y2="62" stroke="#c7a66a" stroke-width="3"/>
      <circle cx="334" cy="62" r="9" fill="#c7a66a"/><path d="M331 57l5 5-5 5" fill="none" stroke="#fff" stroke-width="2"/>
      <circle cx="690" cy="62" r="9" fill="#c7a66a"/><path d="M687 57l5 5-5 5" fill="none" stroke="#fff" stroke-width="2"/>
    </svg>

    <div class="service" style="left:98px;top:180px">
      <div class="service-ring active"><div class="inner">
        <svg width="34" height="40" viewBox="0 0 34 40"><path d="M17 2L3 7v12c0 9 6 15 14 19 8-4 14-10 14-19V7z" fill="#fff"/><path d="M17 8l-8 3v8c0 6 4 10 8 13z" fill="#0d2550"/></svg>
      </div></div>
      <h3>Pup Tonic</h3>
      <p>Enim ipsam voluptatem quia voluptas sit aspernatur aut odit aut fugit, sed quia consequuntur magni dolores eos qui ratione voluptatem sequi nesciunt, Neque...</p>
      <span class="btn-more dark">Read More</span>
    </div>

    <div class="service" style="left:455px;top:180px">
      <div class="service-ring"><div class="inner">
        <svg width="50" height="50" viewBox="0 0 50 50" fill="#c7a66a"><circle cx="20" cy="22" r="11"/><circle cx="20" cy="22" r="4" fill="#f1efea"/><g stroke="#c7a66a" stroke-width="5"><line x1="20" y1="6" x2="20" y2="38"/><line x1="4" y1="22" x2="36" y2="22"/><line x1="9" y1="11" x2="31" y2="33"/><line x1="31" y1="11" x2="9" y2="33"/></g><circle cx="20" cy="22" r="4" fill="#f1efea"/><circle cx="37" cy="37" r="7"/><circle cx="37" cy="37" r="2.5" fill="#f1efea"/></svg>
      </div></div>
      <h3>Pellora Lawsuit</h3>
      <p>Enim ipsam voluptatem quia voluptas sit aspernatur aut odit aut fugit, sed quia consequuntur magni dolores eos qui ratione voluptatem sequi nesciunt, Neque...</p>
      <span class="btn-more">Read More</span>
    </div>

    <div class="service" style="left:811px;top:180px">
      <div class="service-ring"><div class="inner">
        <svg width="44" height="44" viewBox="0 0 44 44" fill="#c7a66a"><rect x="6" y="20" width="8" height="18" rx="1"/><path d="M16 20l7-12c2-3 6-1 5 3l-2 7h10c3 0 4 3 3 5l-4 13c-1 2-2 2-4 2H16z"/></svg>
      </div></div>
      <h3>Driftline 5/8" Leads On Sale</h3>
      <p>Enim ipsam voluptatem quia voluptas sit aspernatur aut odit aut fugit, sed quia consequuntur magni dolores eos qui ratione voluptatem sequi nesciunt, Neque...</p>
      <span class="btn-more">Read More</span>
    </div>
  </section>

  <section class="products">
    <h2 class="section-title">Food Products</h2>
    <svg class="arrow" style="left:46px" width="18" height="62" viewBox="0 0 18 62"><path d="M16 1L2 31l14 30" fill="none" stroke="#c9ceda" stroke-width="1.5"/></svg>
    <svg class="arrow" style="left:1136px" width="18" height="62" viewBox="0 0 18 62"><path d="M2 1l14 30L2 61" fill="none" stroke="#c9ceda" stroke-width="1.5"/></svg>

    <article class="product" style="left:99px">
      <div class="product-photo" role="img" aria-label="White bowl of bone-shaped dog biscuits on a wooden table" style="background:linear-gradient(160deg,#c79a63 0%,#efe6da 45%,#8a6a4a 100%)"></div>
      <span class="price">$24.77</span>
      <h4>Avena</h4>
      <p>Commodo consequat. Duis aute irure dolor in reprehenderit in voluptate velit esse cillum dolore...</p>
    </article>
    <article class="product" style="left:360px">
      <div class="product-photo" role="img" aria-label="Raw meat, carrots and a chew bone beside a blue bowl" style="background:linear-gradient(160deg,#9a6a45 0%,#d9a28c 40%,#3c8fcf 75%,#7a5536 100%)"></div>
      <span class="price">$24.77</span>
      <h4>Hearty Broth</h4>
      <p>Commodo consequat. Duis aute irure dolor in reprehenderit in voluptate velit esse cillum dolore...</p>
    </article>
    <article class="product" style="left:619px">
      <div class="product-photo" role="img" aria-label="Metal bowl filled with colourful dry kibble" style="background:linear-gradient(160deg,#e9edf0 0%,#b8683d 40%,#6f8a4a 65%,#9ea3a8 100%)"></div>
      <span class="price">$24.77</span>
      <h4>Garnet Naturals</h4>
      <p>Commodo consequat. Duis aute irure dolor in reprehenderit in voluptate velit esse cillum dolore...</p>
    </article>
    <article class="product" style="left:880px">
      <div class="product-photo" role="img" aria-label="Assorted chew treats with carrots and greens" style="background:linear-gradient(160deg,#4a5058 0%,#5f8a3c 35%,#e0823a 60%,#d8c3a5 100%)"></div>
      <span class="price">$24.77</span>
      <h4>Maple &amp; Biscuit's</h4>
      <p>Commodo consequat. Duis aute irure dolor in reprehenderit in voluptate velit esse cillum dolore...</p>
    </article>
  </section>

  <section class="news">
    <div class="news-frame">
      <div class="news-photo" role="img" aria-label="Two close-ups of a dog's paws before and after a nail trim"></div>
      <svg class="abs" style="left:10px;top:10px" width="513" height="133" viewBox="0 0 513 133"><circle cx="110" cy="82" r="30" fill="none" stroke="#c0262d" stroke-width="2"/><circle cx="356" cy="82" r="30" fill="none" stroke="#c0262d" stroke-width="2"/></svg>
      <h3 class="news-title">The Larch Critter Depot Dog Wash News and Updates...</h3>
      <p class="news-text">The Larch Critter Depot Dog Wash attendants are always here to help wash your four-legged friends, and trim their nails...but they are also here to help educate all of us! Nail trims are such an essential routine for our pups, especially if they don't run and walk as much as they would in the wild...</p>
      <span class="news-more">View More
        <svg width="10" height="10" viewBox="0 0 10 10" style="vertical-align:-1px"><circle cx="5" cy="5" r="5" fill="#c7a66a"/><path d="M4 3l2 2-2 2" fill="none" stroke="#fff" stroke-width="1.4"/></svg>
      </span>
    </div>
  </section>

  <footer class="site-footer">
    <div class="brand footer-brand abs"><span class="brand-dot"></span>Larch Critter Depot</div>
    <p class="footer-about">Lorem Ipsum is simply dummy text of the commodo consequat. Duis aute irure dolor in reprehenderit in voluptate velit esse cillum dolore eu fugiat nulla pariatur. Excepteur sint occaecat cupidatat non proident, sunt in culpa qui officia deserunt and typesetting text...</p>

    <h4 class="footer-head" style="left:428px">Quick Links</h4>
    <ul class="quick-links">
      <li>Home</li><li>About us</li><li>Dog Wash</li><li>Products</li><li>Resources</li><li>Contact</li>
    </ul>

    <h4 class="footer-head" style="left:597px">Our Latest &nbsp;Blog</h4>
    <div class="blog-item" style="top:76px">
      <div class="blog-thumb" role="img" aria-label="Blog photo of a dog"></div>
      <h5>Lorem Ipsum Simply &nbsp;dummy</h5>
      <span class="date">November 01, 2015</span>
      <span class="comments"><svg width="13" height="11" viewBox="0 0 13 11"><path d="M1 1h11v6H5l-3 3V7H1z" fill="#c9ceda"/></svg>123 Comments</span>
    </div>
    <div class="blog-item" style="top:148px">
      <div class="blog-thumb" role="img" aria-label="Blog photo of a puppy"></div>
      <h5>Lorem Ipsum Simply &nbsp;dummy</h5>
      <span class="date">November 01, 2015</span>
      <span class="comments"><svg width="13" height="11" viewBox="0 0 13 11"><path d="M1 1h11v6H5l-3 3V7H1z" fill="#c9ceda"/></svg>123 Comments</span>
    </div>

    <h4 class="footer-head" style="left:898px">Contact Details</h4>
    <div class="contact-row" style="top:74px">
      <svg width="12" height="16" viewBox="0 0 12 16" style="margin-top:2px"><path d="M6 0a6 6 0 0 0-6 6c0 4 6 10 6 10s6-6 6-10a6 6 0 0 0-6-6z" fill="#e1e4ea"/><circle cx="6" cy="6" r="2.2" fill="#0d2550"/></svg>
      <span>Lena Osterveld dummy text of<br>the printing and type<br>setting street-395001</span>
    </div>
    <div class="contact-row phone" style="top:150px">
      <svg width="14" height="14" viewBox="0 0 14 14" style="margin-top:3px"><path d="M3 0l3 3-2 2c1 2 3 4 5 5l2-2 3 3-2 3C6 14 0 8 0 3z" fill="#e1e4ea"/></svg>
      <span>+123-456-789</span>
    </div>
    <div class="contact-row" style="top:195px">
      <svg width="16" height="12" viewBox="0 0 16 12" style="margin-top:4px"><rect width="16" height="12" fill="#e1e4ea"/><path d="M0 0l8 6 8-6" fill="none" stroke="#0d2550" stroke-width="1.4"/></svg>
      <span>www.info@LarchCritterDepot.com</span>
    </div>
  </footer>

  <div class="bottom-bar">
    <p class="copyright">Copyright 2015 LarchCritterDepot. All Rights Reserved</p>
    <div class="social" aria-label="Social links">
      <span></span><span></span><span></span><span></span><span></span>
    </div>
  </div>

</div>
</body>
</html>
```